SkyvornQ Business Cards and Stationary Design

Need a design for our business cards and stationary. I want to carry on the theme of the logo. I want the business cards to have a design on the back. I would like the business cards and the stationary to carry the same theme, design scheme, and branding

Target Market(s)

Airlines and Maintenance Facilities

Industry/Entity Type

Aviation

Contact Information for Business Card

Name
Position Title
Address: 4827 Trellis Hollow Road, Larkmoor Falls, Oregon, 97381
Office Number
Mobile Number
Email
Website

Font styles to use
Serif
Sans Serif

Colors

Designer to choose colors to be used in the design.

```html
<!DOCTYPE html>
<html lang="en">
<head>
<meta charset="UTF-8">
<title>SkyvornQ Business Card</title>
<link rel="stylesheet" href="https://fonts.googleapis.com/css2?family=Montserrat:wght@500;600;700;800&display=swap">
<style>
  :root {
    --sky-blue: #27a3dc;
    --accent-blue: #2a9fd8;
    --navy: #1b2d5a;
    --ink: #1c1c24;
    --paper: #ffffff;
    --backdrop: #e9e9ec;
  }
  * { margin: 0; padding: 0; box-sizing: border-box; }
  html, body {
    width: 1200px; height: 960px; overflow: hidden;
    background: var(--backdrop);
    font-family: "Montserrat", Arial, sans-serif;
  }
  .canvas { position: relative; width: 1200px; height: 960px; }

  .card {
    position: absolute; left: 270px; width: 664px; height: 380px;
    overflow: hidden;
  }
  .card-front { top: 72px; background: var(--sky-blue); }
  .card-back { top: 509px; background: var(--paper); }

  /* front */
  .front-name {
    position: absolute; left: 0; right: 0; top: 218px; text-align: center;
    color: var(--paper); font-weight: 800; font-size: 46px; letter-spacing: 6px;
    line-height: 56px;
  }
  .front-web {
    position: absolute; left: 0; right: 0; top: 323px; text-align: center;
    color: var(--paper); font-weight: 700; font-size: 15px;
  }

  /* back */
  .name-tab {
    position: absolute; left: 0; top: 58px; width: 9px; height: 62px;
    background: var(--accent-blue); border-radius: 0 6px 6px 0;
  }
  .person-name {
    position: absolute; left: 31px; top: 62px;
    color: var(--accent-blue); font-size: 27px; font-weight: 500;
    line-height: 34px;
  }
  .person-role {
    position: absolute; left: 31px; top: 96px;
    color: var(--ink); font-size: 15px; font-weight: 500;
  }
  .back-name {
    position: absolute; right: 44px; top: 122px;
    color: var(--navy); font-weight: 800; font-size: 25px; letter-spacing: 3.5px;
  }
  .address {
    position: absolute; left: 39px; top: 279px;
    font-style: normal; color: var(--ink); font-size: 16px; line-height: 21px;
    font-weight: 500;
  }
  .contacts {
    position: absolute; left: 429px; top: 255px; list-style: none;
    color: var(--ink); font-size: 16px; line-height: 21.5px; font-weight: 500;
  }
  .contacts .label { color: var(--accent-blue); }
</style>
</head>
<body>
<main class="canvas">
  <section class="card card-front">
    <h1 class="front-name">SKYVORNQ</h1>
    <p class="front-web">www.skyvornq.com</p>
  </section>

  <section class="card card-back">
    <div class="name-tab"></div>
    <h2 class="person-name">Marcus Delane</h2>
    <p class="person-role">Co-Owner</p>
    <p class="back-name">SKYVORNQ</p>
    <address class="address">
      4827 Trellis Hollow Road,<br>
      Larkmoor Falls,<br>
      Oregon, 97381
    </address>
    <ul class="contacts">
      <li><span class="label">M:</span> (541) 555-0148</li>
      <li><span class="label">T:</span> 541-555-0172</li>
      <li><span class="label">E:</span> info@skyvornq.com</li>
      <li><span class="label">W:</span> skyvornq.com</li>
    </ul>
  </section>
</main>
</body>
</html>
```